Brookvale Estates LLC stationary for a real estate property management company.

Create stationary (letterhead, envelopes, business cards) using Brookvale Estates LLC logo as primary creative element. Stationary design needs to be horizontal, leaving as much space as possible for correspondence copy. See attached Creative Brief and past stationary files for details.

Target Market(s)

Prospective apartment residents and current residents, vendors, and government agencies.

Industry/Entity Type

Property Management

Contact Information for Business Card

Business card employee title: Property Manager. Should include address, phone, fax, email, website, slogan, and Brookvale Estates logo.

Font styles to use
Sans Serif

Colors
0592cd
000000

Requirements
Must have
• Tone should be conservative, institutional, business (i.e. banking, finance, real estate). Must include: address, phone, fax, website, and slogan (see attached Creative Brief). Should be a horizontal design, leaving as much room as possible for letter correspondence copy.
Nice to have
• Please use an Arial or Helvetica style font.
Should not have
• Letterhead layout should leave as much room as possible for copy.

```html
<!DOCTYPE html>
<html lang="en">
<head>
<meta charset="utf-8">
<title>Brookvale Estates LLC – Business Card</title>
<link href="https://fonts.googleapis.com/css2?family=Arimo:wght@400;700&display=swap" rel="stylesheet">
<style>
  :root {
    --backdrop: #2b2b2d;
    --card-white: #f7f7f7;
    --brand-blue: #0f78b8;
    --text-grey: #555558;
    --text-dark: #4a4a4d;
    --back-light: #6d6d70;
    --back-dark: #3a3a3c;
    --mark-grey: #4a4a4c;
    --white: #ffffff;
  }
  * { margin: 0; padding: 0; box-sizing: border-box; }
  html, body {
    width: 1200px;
    height: 960px;
    overflow: hidden;
    background: var(--backdrop);
    font-family: "Arimo", Arial, Helvetica, sans-serif;
  }
  .canvas {
    position: relative;
    width: 1200px;
    height: 960px;
  }
  .card {
    position: absolute;
    width: 600px;
    height: 342px;
  }
  .card-front {
    left: 302px;
    top: 129px;
    background: var(--card-white);
  }
  .card-back {
    left: 299px;
    top: 489px;
    background: linear-gradient(135deg, var(--back-light) 0%, var(--back-dark) 55%, var(--back-dark) 100%);
  }
  .front-mark {
    position: absolute;
    left: 492px;
    top: 46px;
    width: 56px;
    height: 56px;
    background: var(--brand-blue);
  }
  .contact {
    position: absolute;
    left: 30px;
    top: 188px;
  }
  .contact-name {
    color: var(--brand-blue);
    font-weight: 700;
    font-size: 20px;
    letter-spacing: 0.2px;
    line-height: 22px;
  }
  .contact-title {
    color: var(--text-grey);
    font-size: 15px;
    line-height: 20px;
    margin-bottom: 8px;
  }
  .contact-line {
    color: var(--text-dark);
    font-size: 13.5px;
    line-height: 18px;
  }
  .slogan {
    color: var(--brand-blue);
    font-weight: 700;
    font-size: 14px;
    margin-top: 8px;
  }
  .back-brand {
    position: absolute;
    left: 0;
    right: 0;
    top: 0;
    bottom: 0;
    display: flex;
    align-items: center;
    justify-content: center;
    gap: 18px;
  }
  .back-mark {
    width: 52px;
    height: 52px;
    background: var(--brand-blue);
  }
  .back-name {
    color: var(--white);
    font-weight: 700;
    font-size: 30px;
    letter-spacing: 1.5px;
  }
</style>
</head>
<body>
  <main class="canvas">
    <section class="card card-front">
      <div class="front-mark"></div>
      <div class="contact">
        <p class="contact-name">DANIEL HARTLEY</p>
        <p class="contact-title">Property Manager</p>
        <p class="contact-line">Phone: 555-214-3071 Fax: 555-214-3072</p>
        <p class="contact-line">daniel@brookvaleestates.us | www.brookvaleestates.us</p>
        <p class="contact-line">2750 Alder Creek Road #B210, Fairview, CA 90000</p>
        <p class="slogan">Multifamily Property Management</p>
      </div>
    </section>
    <section class="card card-back">
      <div class="back-brand">
        <div class="back-mark"></div>
        <p class="back-name">BROOKVALE ESTATES LLC</p>
      </div>
    </section>
  </main>
</body>
</html>
```